Moravel Aesthetic Doctor

I require an elegant, luxurious looking business card for my aesthetic business. I am a doctor and that will set me aside from competitors. I am planning to provide home and spa based treatments to clients with high expectations. I have attached my logo.

```html
<!DOCTYPE html>
<html lang="en">
<head>
<meta charset="utf-8">
<title>Moravel Aesthetic Doctor – Business Card</title>
<link rel="stylesheet" href="https://fonts.googleapis.com/css2?family=Cormorant+Garamond:wght@400;600;700&family=Quicksand:wght@400;500&display=swap">
<style>
  :root {
    --bg: #5a5d62;
    --card: #ffffff;
    --band: #a7a9ac;
    --blue: #1ea0e6;
    --grey-text: #8c8e91;
    --grey-line: #b5b7ba;
    --logo-grey: #8e9093;
  }
  * { box-sizing: border-box; margin: 0; padding: 0; }
  html, body { width: 1200px; height: 965px; overflow: hidden; }
  body { background: var(--bg); position: relative; font-family: "Quicksand", sans-serif; }

  .card {
    position: absolute;
    width: 720px; height: 411px;
    background: var(--card);
    box-shadow: 0 10px 28px rgba(0,0,0,.35);
    overflow: hidden;
  }
  .card-front { left: 60px; top: 45px; }
  .card-back { left: 420px; top: 505px; display: flex; }

  /* Front */
  .brand {
    position: absolute; left: 0; right: 0; top: 80px;
    display: flex; justify-content: center; align-items: center; gap: 20px;
  }
  .brand-ring {
    width: 120px; height: 120px; border-radius: 50%;
    border: 4px solid var(--grey-line); flex: none;
  }
  .brand-name {
    font-family: "Cormorant Garamond", serif; font-weight: 400;
    color: var(--logo-grey); line-height: 1; white-space: nowrap;
  }
  .brand-name .main { display: block; font-size: 70px; letter-spacing: 3px; }
  .brand-name .sub { display: block; font-size: 24px; letter-spacing: 3px; margin-top: 6px; text-transform: uppercase; }

  .services {
    position: absolute; left: 0; right: 0; top: 262px;
    text-align: center; color: var(--blue);
    font-size: 20px; line-height: 1.25;
  }
  .rule { position: absolute; height: 2px; background: var(--grey-line); }
  .rule-right { right: 38px; top: 236px; width: 150px; }
  .rule-left { left: 38px; top: 358px; width: 150px; }

  /* Back */
  .side-band {
    width: 205px; height: 100%; background: var(--band);
    border-right: 2px solid var(--blue);
    position: relative; flex: none;
  }
  .side-brand {
    position: absolute; left: 50%; top: 50%;
    transform: translate(-50%, -50%) rotate(-90deg);
    display: flex; align-items: center; gap: 14px; white-space: nowrap;
  }
  .side-ring { width: 72px; height: 72px; border-radius: 50%; border: 3px solid #ffffff; flex: none; }
  .side-name { font-family: "Cormorant Garamond", serif; color: #ffffff; line-height: 1; }
  .side-name .main { display: block; font-size: 54px; letter-spacing: 3px; }
  .side-name .sub { display: block; font-size: 17px; letter-spacing: 2px; color: var(--blue); text-transform: uppercase; margin-top: 4px; }

  .details { position: relative; flex: 1; padding: 48px 0 0 40px; }
  .person { display: flex; align-items: baseline; gap: 12px; }
  .person-name {
    font-family: "Cormorant Garamond", serif; font-weight: 700;
    font-size: 38px; color: var(--blue);
  }
  .credentials { font-size: 19px; color: var(--grey-text); border-left: 2px solid #444; padding-left: 10px; }
  .diploma { font-size: 19px; color: var(--grey-text); margin-top: 2px; }

  .contact { list-style: none; margin-top: 66px; font-size: 19px; color: var(--grey-text); }
  .contact li { display: flex; align-items: center; gap: 12px; line-height: 1.4; }
  .contact svg { width: 18px; height: 18px; flex: none; }
  .contact b { color: var(--blue); font-weight: 500; }

  .social { position: absolute; right: 60px; top: 158px; display: flex; gap: 12px; }
  .social span { width: 22px; height: 22px; border-radius: 50%; background: var(--blue); }

  .tagline {
    position: absolute; right: 40px; bottom: 40px;
    font-family: "Cormorant Garamond", serif; font-weight: 600;
    font-size: 22px; letter-spacing: 1px; color: var(--blue); text-transform: uppercase;
  }
</style>
</head>
<body>
  <section class="card card-front">
    <div class="brand">
      <div class="brand-ring"></div>
      <div class="brand-name"><span class="main">MORAVEL</span><span class="sub">Aesthetic Doctor</span></div>
    </div>
    <div class="rule rule-right"></div>
    <p class="services">
      Dermal injectables - Plasma facials - Microneedling<br>
      Skin boosters - Excessive sweating<br>
      Home and Spa Based Treatments
    </p>
    <div class="rule rule-left"></div>
  </section>

  <section class="card card-back">
    <div class="side-band">
      <div class="side-brand">
        <div class="side-ring"></div>
        <div class="side-name"><span class="main">MORAVEL</span><span class="sub">Aesthetic Doctor</span></div>
      </div>
    </div>
    <div class="details">
      <div class="person">
        <span class="person-name">Dr Elise Vantor</span>
        <span class="credentials">MRCPCH MD</span>
      </div>
      <p class="diploma">Australasian Diploma of Aesthetic Medicine</p>

      <div class="social"><span></span><span></span></div>

      <ul class="contact">
        <li>
          <svg viewBox="0 0 24 24" fill="none" stroke="#1ea0e6" stroke-width="2"><path d="M5 3h4l2 5-2.5 1.5a11 11 0 0 0 6 6L16 13l5 2v4a2 2 0 0 1-2 2A16 16 0 0 1 3 5a2 2 0 0 1 2-2z"/></svg>
          0800 555 014
        </li>
        <li>
          <svg viewBox="0 0 24 24" fill="none" stroke="#1ea0e6" stroke-width="2"><rect x="3" y="5" width="18" height="14" rx="1"/><path d="M3 6l9 7 9-7"/></svg>
          elise@moravel.co.nz
        </li>
        <li>
          <svg viewBox="0 0 24 24" fill="none" stroke="#1ea0e6" stroke-width="2"><circle cx="12" cy="12" r="9"/><path d="M3 12h18M12 3c3 3 3 15 0 18M12 3c-3 3-3 15 0 18"/></svg>
          <span>www.<b>moravel</b>.co.nz</span>
        </li>
      </ul>

      <p class="tagline">Home and Spa Based Treatments</p>
    </div>
  </section>
</body>
</html>
```